Laser Tattoo Removal Business Cards

We are looking for a professional business card design for a laser tattoo removal business. Ideally looking for a black business card design. The name of the business is Brightline Tattoo Removal. We place our cards at local tattoo shops so we ideally are looking for something trendy/edgy to draw both male and female clientele in.

Target Market(s)

Male/Female ages 18-60

Contact Information for Business Card

black background ideally.. hoping to stay within greys, whites and black

Font styles to use
Serif
Sans Serif

Colors
121212
a9a9a9
5c5c5c
f5f5f5
ffffff
7f7f7f
606060
848484
9d9d9d

Requirements
Must have
• Employee Info:
• Melissa Thornbury
• Chief Executive Offer
• m: 919.537.2846
• w: 919.362.4178
• f: 919.685.3907
• mthornbury@brightlinetattooremoval.example
• Address:
• 4615 Oakmere Pkwy, Suite 210
• Raleigh, NC 27654
• Website:
• www.brightlinetattooremoval.example
Nice to have
• Myabe business name on back or logo on back and employee info on the front

```html
<!DOCTYPE html>
<html lang="en">
<head>
<meta charset="utf-8">
<title>Brightline Tattoo Removal — Business Cards</title>
<link rel="stylesheet" href="https://fonts.googleapis.com/css2?family=Roboto:wght@400;500;700&display=swap">
<style>
  :root {
    --ink: #121212;
    --stone: #a9a9a9;
    --slate: #5c5c5c;
    --paper: #f5f5f5;
    --white: #ffffff;
    --mid: #7f7f7f;
    --graphite: #606060;
    --ash: #848484;
    --fog: #9d9d9d;
    --backdrop: #3a3431;
  }
  * { margin: 0; padding: 0; box-sizing: border-box; }
  html, body { width: 1200px; height: 769px; overflow: hidden; }
  body {
    background: var(--backdrop);
    font-family: "Roboto", sans-serif;
    position: relative;
  }
  .card {
    position: absolute;
    top: 236px;
    width: 520px;
    height: 297px;
    border-radius: 2px;
  }
  .card--front { left: 50px; background: var(--paper); }
  .card--back  { left: 630px; background: var(--ink); }

  .brand {
    position: absolute;
    display: flex;
    flex-direction: column;
    align-items: center;
    text-align: center;
  }
  .brand__name {
    font-family: "Roboto", sans-serif;
    font-weight: 400;
    text-transform: uppercase;
    letter-spacing: 3px;
    line-height: 1.25;
  }
  .brand__mark {
    width: 10px; height: 10px;
    border-radius: 50%;
    margin-bottom: 10px;
  }
  .card--front .brand { left: 20px; top: 102px; width: 230px; }
  .card--front .brand__name { font-size: 19px; color: var(--ink); }
  .card--front .brand__mark { background: var(--graphite); }

  .divider {
    position: absolute;
    left: 266px; top: 32px;
    width: 1px; height: 233px;
    background: var(--stone);
  }

  .contact { position: absolute; left: 290px; top: 42px; width: 220px; }
  .contact__name {
    font-weight: 700; font-size: 17px; color: var(--ink);
    letter-spacing: 0.2px;
  }
  .contact__title { font-size: 12.5px; color: var(--fog); margin-top: 1px; }
  .contact__address { font-size: 12.5px; color: var(--graphite); margin-top: 6px; line-height: 1.35; }
  .contact__list { list-style: none; margin-top: 6px; }
  .contact__item {
    display: flex; align-items: center; gap: 8px;
    font-size: 12.5px; color: var(--graphite); line-height: 18px;
  }
  .contact__item--small { font-size: 10px; letter-spacing: -0.1px; }
  .contact__icon { width: 11px; height: 11px; flex: none; fill: var(--ink); }

  .card--back .brand { left: 60px; top: 92px; width: 400px; }
  .card--back .brand__name { font-size: 24px; color: var(--paper); }
  .card--back .brand__mark { background: var(--stone); }
  .web {
    position: absolute; left: 0; right: 0; top: 222px;
    text-align: center;
    font-size: 11.5px; letter-spacing: 2.4px; color: var(--paper);
  }
</style>
</head>
<body>
  <section class="card card--front" aria-label="Business card front">
    <div class="brand">
      <span class="brand__mark"></span>
      <span class="brand__name">Brightline<br>Tattoo Removal</span>
    </div>
    <div class="divider"></div>
    <div class="contact">
      <p class="contact__name">MELISSA THORNBURY</p>
      <p class="contact__title">Chief Executive Offer</p>
      <p class="contact__address">4615 Oakmere Pkwy, Suite 210<br>Raleigh, NC 27654</p>
      <ul class="contact__list">
        <li class="contact__item">
          <svg class="contact__icon" viewBox="0 0 12 12"><path d="M2.5 0.8l2 2-1 1.4c0.8 1.7 2 2.9 3.7 3.7l1.4-1 2 2-1.4 2C4.7 10.6 1.4 7.3 0.6 2.2z"/></svg>
          <span>919.362.4178</span>
        </li>
        <li class="contact__item">
          <svg class="contact__icon" viewBox="0 0 12 12"><path d="M3 0h6v12H3zM4 1.5v8h4v-8z"/></svg>
          <span>919.537.2846</span>
        </li>
        <li class="contact__item">
          <svg class="contact__icon" viewBox="0 0 12 12"><path d="M3 0h6v3H3zM0 4h12v6h-2v2H2v-2H0zM3 8v3h6V8z"/></svg>
          <span>919.685.3907</span>
        </li>
        <li class="contact__item contact__item--small">
          <svg class="contact__icon" viewBox="0 0 12 12"><path d="M0 2h12v8H0zM1 3l5 3.6L11 3z" fill-rule="evenodd"/></svg>
          <span>mthornbury@brightlinetattooremoval.example</span>
        </li>
        <li class="contact__item contact__item--small">
          <svg class="contact__icon" viewBox="0 0 12 12"><circle cx="6" cy="6" r="5.5"/><path d="M0.5 6h11M6 0.5c-2.5 3-2.5 8 0 11M6 0.5c2.5 3 2.5 8 0 11" stroke="#f5f5f5" stroke-width="0.9" fill="none"/></svg>
          <span>www.brightlinetattooremoval.example</span>
        </li>
      </ul>
    </div>
  </section>

  <section class="card card--back" aria-label="Business card back">
    <div class="brand">
      <span class="brand__mark"></span>
      <span class="brand__name">Brightline<br>Tattoo Removal</span>
    </div>
    <p class="web">www.brightlinetattooremoval.example</p>
  </section>
</body>
</html>
```